Health and wellnes company needs business cards

We are a Health and wellness business just relocated to Spain. Here nobody knows our business so we would like to put some of our services on the card. Clean design with logo.

Contact Information for Business Card

Brightmeadow
Paula & Oskar Dunbeck
Calle del Almendro 57
Villamar de la Costa
Mobile: 0046 731 402687
info@brightmeadow.example

Font styles to use
Serif

Colors
85cae6
85acd3
b768aa

Requirements
Must have
• these Services somewhere on the card
• - Private or group yoga
• - Reconnective healing
• - Kitesurfing lessons
• - Massage
• LOgo somewhere
Nice to have
• Colours that go with the logo please

```html
<!DOCTYPE html>
<html lang="en">
<head>
<meta charset="utf-8">
<title>Brightmeadow business card</title>
<link rel="stylesheet" href="https://fonts.googleapis.com/css2?family=Cinzel:wght@500;600&family=Mulish:wght@400;500&display=swap">
<style>
  :root {
    --navy: #1f3c6b;
    --teal: #72c6c8;
    --grey-text: #626262;
    --fold: #a9a9a9;
    --paper: #ffffff;
    --backdrop: #e4e4e4;
  }
  html, body {
    margin: 0;
    width: 1200px;
    height: 893px;
    overflow: hidden;
    background: var(--backdrop);
  }
  .card {
    position: absolute;
    left: 93px;
    top: 288px;
    width: 1025px;
    height: 291px;
    background: var(--paper);
    box-shadow: 0 2px 6px rgba(0,0,0,0.18);
    overflow: hidden;
  }
  .card__back, .card__front {
    position: absolute;
    top: 0;
    height: 100%;
  }
  .card__back { left: 0; width: 513px; }
  .card__front { left: 513px; width: 512px; }
  .fold {
    position: absolute;
    left: 512px;
    top: 0;
    width: 2px;
    height: 100%;
    background: var(--fold);
    z-index: 2;
  }
  .ring-decor {
    position: absolute;
    left: 0;
    top: 0;
    width: 1025px;
    height: 291px;
    z-index: 1;
  }
  .owners {
    position: absolute;
    left: 27px;
    top: 43px;
    margin: 0;
    font-family: "Cinzel", serif;
    font-weight: 600;
    font-size: 13.5px;
    letter-spacing: 0.2px;
    color: var(--navy);
    z-index: 3;
  }
  .owners__surname { color: var(--teal); }
  .address {
    position: absolute;
    left: 27px;
    top: 84px;
    margin: 0;
    font-family: "Mulish", sans-serif;
    font-style: normal;
    font-size: 12.5px;
    line-height: 14.5px;
    color: var(--grey-text);
    z-index: 3;
  }
  .contacts {
    position: absolute;
    left: 27px;
    top: 139px;
    margin: 0;
    padding: 0;
    list-style: none;
    font-family: "Mulish", sans-serif;
    font-size: 12.5px;
    line-height: 14.5px;
    color: var(--grey-text);
    z-index: 3;
  }
  .contacts li { display: flex; align-items: center; gap: 6px; }
  .contacts svg { width: 10px; height: 10px; fill: var(--navy); flex: none; }
  .services {
    position: absolute;
    left: 27px;
    top: 194px;
    margin: 0;
    padding: 0;
    list-style: none;
    font-family: "Mulish", sans-serif;
    font-weight: 500;
    font-size: 12.5px;
    line-height: 14.5px;
    color: var(--navy);
    z-index: 3;
  }
  .services li::before {
    content: "";
    display: inline-block;
    width: 4px;
    height: 4px;
    border-radius: 50%;
    background: var(--teal);
    margin: 0 6px 2px 1px;
    vertical-align: middle;
  }
  .brand {
    position: absolute;
    left: 0;
    top: 0;
    width: 100%;
    height: 100%;
    display: flex;
    flex-direction: column;
    align-items: center;
    justify-content: center;
    padding-left: 212px;
    padding-top: 12px;
    box-sizing: border-box;
  }
  .brand__mark {
    width: 84px;
    height: 84px;
    border: 5px solid var(--teal);
    border-radius: 50%;
    box-sizing: border-box;
    margin-bottom: 10px;
  }
  .brand__name {
    margin: 0;
    font-family: "Cinzel", serif;
    font-weight: 600;
    font-size: 23px;
    letter-spacing: 0.3px;
    color: var(--navy);
  }
</style>
</head>
<body>
  <main class="card">
    <svg class="ring-decor" viewBox="0 0 1025 291" aria-hidden="true">
      <defs>
        <linearGradient id="ringTone" x1="0" y1="0" x2="0" y2="1">
          <stop offset="0" stop-color="#82cfd0"/>
          <stop offset="1" stop-color="#6ac2c3"/>
        </linearGradient>
      </defs>
      <circle cx="513" cy="145" r="139" fill="none" stroke="url(#ringTone)" stroke-width="18"/>
    </svg>
    <div class="fold"></div>

    <section class="card__back">
      <h2 class="owners">PAULA &amp; <span class="owners__surname">OSKAR DUNBECK</span></h2>
      <address class="address">Calle del<br>Almendro 57 Villamar<br>de la Costa</address>
      <ul class="contacts">
        <li><svg viewBox="0 0 10 10"><path d="M2.5 0h5a1 1 0 0 1 1 1v8a1 1 0 0 1-1 1h-5a1 1 0 0 1-1-1V1a1 1 0 0 1 1-1zm0.6 1.3v6.4h3.8V1.3z"/></svg>0046 731 402687</li>
        <li><svg viewBox="0 0 10 10"><path d="M0 2h10v6H0zM1 3v.4l4 2.4 4-2.4V3z" fill-rule="evenodd"/></svg>info@brightmeadow.example</li>
        <li><svg viewBox="0 0 10 10"><circle cx="5" cy="5" r="4.5"/><path d="M3 3.2c1 .2 1.6.8 1.4 1.8L3.3 6.3 2.5 4.6zM5.8 1.6c.9.2 1.7.9 2 1.7l-1.3.4-1-1z" fill="#fff"/></svg>www.brightmeadow.example</li>
      </ul>
      <ul class="services">
        <li>Private or group yoga</li>
        <li>Reconnective healing</li>
        <li>Kitesurfing lessons</li>
        <li>Massage</li>
      </ul>
    </section>

    <section class="card__front">
      <div class="brand">
        <div class="brand__mark"></div>
        <h1 class="brand__name">BRIGHTMEADOW</h1>
      </div>
    </section>
  </main>
</body>
</html>
```